Website for courses for men for making money, health, fitness

I require a website which is going to be a mix of a crypto currency website and website aimed at providing men with money making, health, relationship advice courses and content

The name isn't decided yet so for now please call it something like

KESTREL YARD

A platform dedicated to making men wealthy, physically strong, mentally tough & successful with women

In the top right, I need it to show how many points they have, they must buy points in order to use them to claim the courses.

WHAT WE DO

Kestrel yard is a platform where you can learn everything you need about business, making money, crypto currency, fitness, health, mental toughness and resilience and how to be successful with women all in one place

HOW WILL THIS WORK & WHY SHOULD I BUY POINTS?

xxxxxxxxxxxxxxxxxxxxxxxx
xxxxxxxxxxxxxxxxxxxxxxx
xxxxxxxxxxxxxxxxxxxxx

AFFILIATE SCHEME

EARN UP TO $125 DOLLARS PER PERSON WHO SIGNS UP THROUGH YOUR LINK

START EARNING NOW - button
______________________________________________________

BUY POINTS
(A maximum of only $250 worth of points can be purchased per person until the platform goes fully live)

ROAD MAP & THE MODEL

2023

Q1 - PRE BUY IN FOR POINTS

Q2 - FULL WEBSITE LAUNCH

Q3 - APP LAUNCH

Q4 - IN APP ADVERT LAUNCH

It must have a very slick and sharp eye catching look, and be designed to convert people into purchasing points

some ideas of the feel of the website -

https://brivaloo.io/
https://nestorly.style/
https://plumwick.trelvanta.com/

```html
<!DOCTYPE html>
<html lang="en">
<head>
<meta charset="utf-8">
<title>Kestrel Yard</title>
<link href="https://fonts.googleapis.com/css2?family=Archivo:wght@700;800;900&family=Montserrat:wght@400;500;600;700&display=swap" rel="stylesheet">
<style>
:root{
  --blue:#1a6ec6;
  --blue-dark:#0d3f8f;
  --navy:#0b1528;
  --yellow:#f7d93c;
  --ink:#1c1c1c;
  --grey-bg:#f2f3f5;
  --footer:#161616;
  --muted:#444;
}
*{box-sizing:border-box;margin:0;padding:0}
html,body{width:1200px;height:4773px;overflow:hidden}
body{position:relative;font-family:'Montserrat',sans-serif;color:var(--ink);background:#fff}
.abs{position:absolute}
h1,h2,h3,.head{font-family:'Archivo',sans-serif;font-weight:800}
section{position:absolute;left:0;width:1200px;overflow:hidden}
.btn{position:absolute;display:flex;align-items:center;justify-content:center;gap:14px;background:var(--blue);color:#fff;border-radius:30px;font-weight:600;font-size:21px;text-decoration:underline;text-underline-offset:4px}
.btn svg{width:26px;height:14px}
.swoosh{position:absolute;pointer-events:none}

/* header */
.site-header{top:0;height:87px;background:#fff}
.logo{position:absolute;left:68px;top:26px;font-family:'Archivo',sans-serif;font-weight:900;font-size:31px;color:var(--blue-dark);letter-spacing:-.5px}
.lang{position:absolute;left:963px;top:22px;width:80px;height:39px;border-radius:20px;background:#e9e9ec;display:flex;align-items:center;gap:8px;padding-left:10px;font-size:14px;font-weight:600;color:#555}
.menu{position:absolute;left:1088px;top:32px}

/* hero */
.hero{top:87px;height:723px;background:linear-gradient(120deg,#15213a 0%,var(--navy) 55%,#08101f 100%)}
.hero-photo{position:absolute;left:160px;top:0;width:420px;height:723px;background:radial-gradient(circle at 45% 35%,#c99a38 0,#8a6322 22%,#3a2a20 45%,transparent 70%)}
.hero .welcome{position:absolute;left:637px;top:218px;color:#fff;font-family:'Archivo',sans-serif;font-weight:700;font-size:56px}
.hero h1{position:absolute;left:637px;top:308px;color:#fff;font-size:56px;font-weight:900;letter-spacing:1px}
.dots{position:absolute;left:548px;top:661px;display:flex;gap:14px;align-items:center}
.dots i{width:9px;height:9px;border-radius:50%;background:#fff;display:block}
.dots i.on{width:18px;height:18px;border:2px solid #fff;background:transparent;position:relative}
.dots i.on::after{content:"";position:absolute;left:3px;top:3px;width:8px;height:8px;border-radius:50%;background:#fff}

/* intro */
.intro{top:810px;height:310px;text-align:center}
.intro h2{position:absolute;top:52px;width:100%;font-size:42px;font-weight:900}
.intro p{position:absolute;top:130px;width:100%;font-size:23px;font-weight:500}
.pills{position:absolute;top:199px;left:70px;display:flex;gap:14px}
.pill{height:48px;border:2px solid #e2e2e2;border-radius:4px;display:flex;align-items:center;gap:14px;padding:0 20px;font-size:18px;font-weight:500;box-shadow:0 2px 4px rgba(0,0,0,.06)}

/* what we do */
.what{top:1120px;height:525px;background:var(--grey-bg)}
.hex-photo{position:absolute}
.what h2{position:absolute;left:526px;top:98px;font-size:40px}
.what p{position:absolute;left:530px;top:165px;width:500px;font-size:20.5px;line-height:34.5px;color:#333}

/* how */
.how{top:1645px;height:995px}
.how h2{position:absolute;top:80px;width:100%;text-align:center;font-size:38px;line-height:58px}
.how .lead{position:absolute;top:224px;left:180px;width:840px;text-align:center;font-size:21px;line-height:34.5px;color:#333}
.step{position:absolute;width:180px}
.step h3{font-family:'Montserrat',sans-serif;font-weight:700;font-size:17px;color:#1d3a6b;margin-bottom:14px}
.step p{font-size:15.5px;line-height:30px;color:#333}
.ring{position:absolute}

/* affiliate */
.affiliate{top:2640px;height:523px;background:var(--grey-bg)}
.affiliate h2{position:absolute;left:133px;top:72px;font-size:40px}
.affiliate .sub{position:absolute;left:133px;top:137px;font-size:26.5px;line-height:38px;font-weight:500}
.affiliate p{position:absolute;left:133px;top:228px;width:510px;font-size:21px;line-height:35px;color:#333}

/* buy points */
.points{top:3163px;height:682px}
.points h2{position:absolute;left:580px;top:122px;font-size:40px}
.points .sub{position:absolute;left:583px;top:186px;width:470px;font-size:27.5px;line-height:38.5px;font-weight:500}
.points p{position:absolute;left:583px;top:362px;width:500px;font-size:21px;line-height:34.5px;color:#333}

/* roadmap */
.roadmap{top:3845px;height:602px;background:var(--grey-bg)}
.roadmap h2{position:absolute;top:52px;width:100%;text-align:center;font-size:40px}
.bar{position:absolute;top:365px;height:14px;border-radius:7px}
.node{position:absolute;width:80px;height:80px;border-radius:50%;background:#fff;display:flex;align-items:center;justify-content:center;font-family:'Montserrat',sans-serif;font-size:33px;font-weight:500;border:4px solid var(--blue)}
.node.y{border-color:var(--yellow)}
.stem{position:absolute;width:2px}
.milestone{position:absolute;width:260px;text-align:center}
.milestone h4{font-size:17px;font-weight:600;margin-bottom:8px}
.milestone p{font-size:15.5px;line-height:30px;color:#333}

/* footer */
.site-footer{top:4447px;height:326px;background:var(--footer);color:#e8e8e8}
.f-about{position:absolute;left:109px;top:82px;width:190px;font-size:15.5px;line-height:30px}
.f-col{position:absolute;top:60px}
.f-col h5{font-family:'Archivo',sans-serif;font-size:16px;font-weight:800;letter-spacing:.5px;margin-bottom:18px}
.f-col li{list-style:none;font-size:17px;line-height:34px}
.vline{position:absolute;top:52px;width:1px;height:165px;background:#555}
.f-rule{position:absolute;left:109px;right:109px;top:273px;height:1px;background:#444}
.copy{position:absolute;top:290px;width:100%;text-align:center;font-size:13px}
</style>
</head>
<body>

<header class="site-header abs" style="width:1200px">
  <div class="logo">KESTREL YARD</div>
  <div class="lang">
    <svg width="22" height="22" viewBox="0 0 22 22"><clipPath id="fc"><circle cx="11" cy="11" r="11"/></clipPath><g clip-path="url(#fc)"><rect width="22" height="8" fill="#111"/><rect y="7.3" width="22" height="7.4" fill="#dd1f26"/><rect y="14.6" width="22" height="7.4" fill="#ffce00"/></g></svg>
    GER
  </div>
  <svg class="menu" width="30" height="22" viewBox="0 0 30 22"><g stroke="#222" stroke-width="2.6" stroke-linecap="round"><line x1="2" y1="3" x2="28" y2="3"/><line x1="9" y1="11" x2="28" y2="11"/><line x1="2" y1="19" x2="28" y2="19"/></g></svg>
</header>

<section class="hero">
  <div class="hero-photo" role="img" aria-label="Hand holding up a gold coin against a dark background"></div>
  <svg class="swoosh" style="left:0;top:0" width="1200" height="723" viewBox="0 0 1200 723">
    <path d="M840 723 Q1080 650 1200 470 L1200 540 Q1110 670 950 723Z" fill="#fff"/>
    <path d="M920 723 Q1110 640 1200 520 L1200 610 Q1130 690 1030 723Z" fill="var(--yellow)"/>
    <path d="M1030 723 Q1140 680 1200 610 L1200 723Z" fill="var(--blue)"/>
  </svg>
  <div class="welcome">Welcome To</div>
  <h1>KESTREL YARD</h1>
  <a class="btn" style="left:639px;top:404px;width:213px;height:52px">Get Started
    <svg viewBox="0 0 26 14"><path d="M1 7h22M17 1l6 6-6 6" fill="none" stroke="#fff" stroke-width="2"/></svg></a>
  <div class="dots"><i></i><i class="on"></i><i></i><i></i></div>
</section>

<section class="intro">
  <h2>KESTREL YARD</h2>
  <p>A PLATFORM DEDICATED TO MAKING MEN</p>
  <div class="pills">
    <div class="pill"><svg width="18" height="18" viewBox="0 0 18 18"><circle cx="9" cy="9" r="7.5" fill="none" stroke="#333" stroke-width="1.5"/><path d="M5.5 9l2.5 2.5 4.5-5" fill="none" stroke="#333" stroke-width="1.5"/></svg>WEALTHY</div>
    <div class="pill"><svg width="18" height="18" viewBox="0 0 18 18"><circle cx="9" cy="9" r="7.5" fill="none" stroke="#333" stroke-width="1.5"/><path d="M5.5 9l2.5 2.5 4.5-5" fill="none" stroke="#333" stroke-width="1.5"/></svg>PHYSICALLY STRONG</div>
    <div class="pill"><svg width="18" height="18" viewBox="0 0 18 18"><circle cx="9" cy="9" r="7.5" fill="none" stroke="#333" stroke-width="1.5"/><path d="M5.5 9l2.5 2.5 4.5-5" fill="none" stroke="#333" stroke-width="1.5"/></svg>MENTALLY TOUGH</div>
    <div class="pill"><svg width="18" height="18" viewBox="0 0 18 18"><circle cx="9" cy="9" r="7.5" fill="none" stroke="#333" stroke-width="1.5"/><path d="M5.5 9l2.5 2.5 4.5-5" fill="none" stroke="#333" stroke-width="1.5"/></svg>SUCCESSFUL WITH WOMEN</div>
  </div>
</section>

<section class="what">
  <svg class="swoosh" style="left:0;top:0" width="1200" height="525" viewBox="0 0 1200 525">
    <path d="M0 0 H190 Q60 40 0 150Z" fill="var(--yellow)"/>
    <path d="M0 0 H110 Q30 30 0 70Z" fill="var(--blue)"/>
    <path d="M1200 230 Q1130 430 860 525 H1200Z" fill="var(--yellow)"/>
    <path d="M1200 320 Q1140 460 990 525 H1200Z" fill="#fff"/>
    <path d="M1200 380 Q1150 480 1070 525 H1200Z" fill="var(--blue-dark)"/>
  </svg>
  <svg class="hex-photo" style="left:83px;top:38px" width="364" height="446" viewBox="0 0 364 446" role="img" aria-label="Portrait of a bearded man in a suit writing at a desk">
    <defs><linearGradient id="g1" x1="0" y1="0" x2="1" y2="1"><stop offset="0" stop-color="#7a6a5c"/><stop offset=".5" stop-color="#2b3850"/><stop offset="1" stop-color="#c9c6c2"/></linearGradient></defs>
    <polygon points="182,0 364,105 364,340 182,446 0,340 0,105" fill="url(#g1)"/>
  </svg>
  <h2>WHAT WE DO</h2>
  <p>Kestrel yard is a platform where you can learn everything you need about business, making money, crypto currency, fitness, health, mental toughness and resilience and how to be successful with women all in one place</p>
  <a class="btn" style="left:520px;top:362px;width:210px;height:52px">Read More
    <svg viewBox="0 0 26 14"><path d="M1 7h22M17 1l6 6-6 6" fill="none" stroke="#fff" stroke-width="2"/></svg></a>
</section>

<section class="how">
  <h2>HOW WILL THIS WORK &amp;<br>WHY SHOULD I BUY POINTS?</h2>
  <p class="lead">Lorem Ipsum is simply dummy text of the printing and typesetting industry. Lorem Ipsum has been the industry's standard dummy text ever since the 1500s, when an unknown printer took a galley of type and scrambled it to make a type specimen book. It has survived not only five centuries, but also the leap into electronic typesetting, remaining essentially unchanged.</p>

  <svg class="swoosh" style="left:0;top:0" width="1200" height="995" viewBox="0 0 1200 995">
    <path d="M250 530 Q320 520 376 512" fill="none" stroke="#bbb" stroke-width="2"/>
    <path d="M534 530 Q600 545 640 562" fill="none" stroke="#bbb" stroke-width="2" stroke-dasharray="5 4"/>
    <path d="M797 580 Q870 560 902 536" fill="none" stroke="#bbb" stroke-width="2"/>
  </svg>

  <svg class="ring" style="left:101px;top:506px" width="180" height="180" viewBox="0 0 180 180">
    <circle cx="90" cy="90" r="74" fill="none" stroke="var(--yellow)" stroke-width="10"/>
    <path d="M16 90 A74 74 0 0 0 164 90" fill="none" stroke="#37b8e8" stroke-width="10"/>
    <circle cx="90" cy="90" r="64" fill="#fff"/>
    <g fill="none" stroke="#1d3a6b" stroke-width="3"><rect x="58" y="64" width="64" height="42" rx="3"/><path d="M80 106v10M100 106v10M72 118h36"/><rect x="68" y="74" width="30" height="20"/></g>
    <circle cx="158" cy="138" r="16" fill="var(--yellow)"/><text x="158" y="144" text-anchor="middle" font-size="16" fill="#fff" font-family="Montserrat">01</text>
  </svg>
  <svg class="ring" style="left:364px;top:423px" width="180" height="180" viewBox="0 0 180 180">
    <circle cx="90" cy="90" r="74" fill="none" stroke="var(--yellow)" stroke-width="10"/>
    <path d="M16 90 A74 74 0 0 0 164 90" fill="none" stroke="#37b8e8" stroke-width="10"/>
    <circle cx="90" cy="90" r="64" fill="#fff"/>
    <g fill="none" stroke="#1d3a6b" stroke-width="3"><rect x="56" y="72" width="44" height="42" rx="3"/><path d="M64 84h28M64 94h28M64 104h18"/><path d="M98 72v-14l8-6 2 14h14v20h-24z"/></g>
    <circle cx="158" cy="138" r="16" fill="var(--yellow)"/><text x="158" y="144" text-anchor="middle" font-size="16" fill="#fff" font-family="Montserrat">02</text>
  </svg>
  <svg class="ring" style="left:627px;top:506px" width="180" height="180" viewBox="0 0 180 180">
    <circle cx="90" cy="90" r="74" fill="none" stroke="var(--yellow)" stroke-width="10"/>
    <path d="M16 90 A74 74 0 0 0 164 90" fill="none" stroke="#37b8e8" stroke-width="10"/>
    <circle cx="90" cy="90" r="64" fill="#fff"/>
    <g fill="none" stroke="#1d3a6b" stroke-width="3"><path d="M90 56l30 10v22c0 20-14 30-30 36-16-6-30-16-30-36V66z"/><circle cx="90" cy="88" r="14"/><path d="M83 88l5 5 9-10"/></g>
    <circle cx="158" cy="138" r="16" fill="var(--yellow)"/><text x="158" y="144" text-anchor="middle" font-size="16" fill="#fff" font-family="Montserrat">03</text>
  </svg>
  <svg class="ring" style="left:890px;top:423px" width="180" height="180" viewBox="0 0 180 180">
    <circle cx="90" cy="90" r="74" fill="none" stroke="var(--yellow)" stroke-width="10"/>
    <path d="M16 90 A74 74 0 0 0 164 90" fill="none" stroke="#37b8e8" stroke-width="10"/>
    <circle cx="90" cy="90" r="64" fill="#fff"/>
    <g fill="none" stroke="#1d3a6b" stroke-width="3"><circle cx="100" cy="68" r="14"/><path d="M100 60v16M96 64h7a3 3 0 0 1 0 6h-6a3 3 0 0 0 0 6h7"/><path d="M56 108l14-14h18l14 6h-16M56 108l8 8 14-8h20l20-16-6-4-18 10"/></g>
    <circle cx="158" cy="138" r="16" fill="var(--yellow)"/><text x="158" y="144" text-anchor="middle" font-size="16" fill="#fff" font-family="Montserrat">04</text>
  </svg>

  <div class="step" style="left:109px;top:696px"><h3>One Time Register</h3><p>t is a long established fact that a reader will be distracted by the readable content of a page when looking at its layout</p></div>
  <div class="step" style="left:372px;top:619px"><h3>Verification Process</h3><p>Lorem Ipsum is simply dummy text of the printing</p></div>
  <div class="step" style="left:636px;top:696px"><h3>Unique check code</h3><p>It is a long established fact that a reader will be distracted by the readable content of a page when looking at its layout.</p></div>
  <div class="step" style="left:926px;top:619px"><h3>Buy Bitcoins</h3><p>The point of using Lorem Ipsum is that it has a more-or-less normal distribution of letters, as opposed to using 'Content here, content here</p></div>
</section>

<section class="affiliate">
  <svg class="swoosh" style="left:0;top:0" width="1200" height="523" viewBox="0 0 1200 523">
    <path d="M0 0 H180 Q60 40 0 140Z" fill="var(--yellow)"/>
    <path d="M0 0 H100 Q30 30 0 65Z" fill="var(--blue)"/>
  </svg>
  <h2>AFFILIATE SCHEME</h2>
  <div class="sub">EARN UP TO $125 DOLLARS PER PERSON<br>WHO SIGNS UP THROUGH YOUR LINK</div>
  <p>It is a long established fact that a reader will be distracted by the readable content of a page when looking at its layout.</p>
  <a class="btn" style="left:122px;top:355px;width:317px;height:52px">START EARNING NOW
    <svg viewBox="0 0 26 14"><path d="M1 7h22M17 1l6 6-6 6" fill="none" stroke="#fff" stroke-width="2"/></svg></a>
  <svg class="hex-photo" style="left:695px;top:27px" width="400" height="460" viewBox="0 0 400 460" role="img" aria-label="Older man and young woman looking at a tablet together">
    <defs><linearGradient id="g2" x1="0" y1="0" x2="1" y2="1"><stop offset="0" stop-color="#e6e1d6"/><stop offset=".5" stop-color="#8b7668"/><stop offset="1" stop-color="#3a3a42"/></linearGradient></defs>
    <polygon points="200,2 398,116 398,344 200,458 2,344 2,116" fill="var(--yellow)"/>
    <polygon points="200,14 388,122 388,338 200,446 12,338 12,122" fill="url(#g2)"/>
  </svg>
</section>

<section class="points">
  <svg class="swoosh" style="left:0;top:0" width="560" height="682" viewBox="0 0 560 682">
    <circle cx="307" cy="310" r="180" fill="#d9ecfa"/>
    <circle cx="307" cy="310" r="150" fill="#bcdcf4"/>
  </svg>
  <div class="abs" style="left:207px;top:60px;width:247px;height:500px;border-radius:30px;border:6px solid #e9edf2;background:linear-gradient(#2235c9 0 40px,#fff 40px);box-shadow:0 10px 30px rgba(0,0,0,.15)" role="img" aria-label="Phone showing a crypto portfolio app screen"></div>
  <h2>BUY POINTS</h2>
  <div class="sub">A maximum of only $250 worth of points can be purchased per person until the platform goes fully live</div>
  <p>Lorem Ipsum is simply dummy text of the printing and typesetting industry. Lorem Ipsum has been the industry's standard dummy text ever since the 1500s,</p>
</section>

<section class="roadmap">
  <svg class="swoosh" style="left:0;top:0" width="1200" height="602" viewBox="0 0 1200 602">
    <path d="M0 0 H180 Q60 40 0 130Z" fill="var(--yellow)"/>
    <path d="M0 0 H100 Q30 30 0 60Z" fill="var(--blue)"/>
    <path d="M1200 430 Q1150 550 1040 602 H1200Z" fill="var(--blue-dark)"/>
  </svg>
  <h2>ROAD MAP &amp; THE MODEL (2022)</h2>

  <div class="bar" style="left:94px;width:246px;background:var(--blue)"></div>
  <div class="bar" style="left:342px;width:246px;background:var(--yellow)"></div>
  <div class="bar" style="left:590px;width:246px;background:var(--blue)"></div>
  <div class="bar" style="left:838px;width:240px;background:var(--yellow)"></div>

  <div class="stem" style="left:216px;top:289px;height:76px;background:var(--blue)"></div>
  <div class="stem" style="left:708px;top:289px;height:76px;background:var(--blue)"></div>
  <div class="stem" style="left:462px;top:379px;height:76px;background:var(--yellow)"></div>
  <div class="stem" style="left:955px;top:379px;height:76px;background:var(--yellow)"></div>
  <svg class="swoosh" style="left:0;top:0" width="1200" height="602" viewBox="0 0 1200 602">
    <path d="M208 379l9 9 9-9Z" fill="var(--blue)"/>
    <path d="M700 379l9 9 9-9Z" fill="var(--blue)"/>
    <path d="M454 365l9-9 9 9Z" fill="var(--yellow)"/>
    <path d="M947 365l9-9 9 9Z" fill="var(--yellow)"/>
  </svg>

  <div class="node" style="left:177px;top:209px">01</div>
  <div class="node" style="left:669px;top:209px">03</div>
  <div class="node y" style="left:423px;top:454px">02</div>
  <div class="node y" style="left:916px;top:454px">04</div>

  <div class="milestone" style="left:329px;top:208px"><h4>FULL WEBSITE LAUNCH</h4><p>it is a long established<br>fact that a reader its<br>layout.</p></div>
  <div class="milestone" style="left:827px;top:272px"><h4>IN APP ADVERT LAUNCH</h4><p>it is a long established fact</p></div>
  <div class="milestone" style="left:85px;top:421px"><h4>PRE BUY IN FOR POINTS</h4><p>it is a long established<br>fact that a reader its<br>layout.</p></div>
  <div class="milestone" style="left:581px;top:413px"><h4>APP LAUNCH</h4><p>it is a long established<br>fact that a reader its<br>layout.</p></div>
</section>

<footer class="site-footer abs" style="left:0;width:1200px">
  <p class="f-about">A platform dedicated to making men wealthy, physically strong, mentally tough &amp; successful with women</p>
  <div class="vline" style="left:317px"></div>
  <div class="vline" style="left:543px"></div>
  <div class="vline" style="left:757px"></div>
  <div class="f-col" style="left:369px"><h5>OTHER LINKS</h5><ul><li>Privacy Policy</li><li>Disclaimer</li><li>FAQ</li><li>Terms</li></ul></div>
  <div class="f-col" style="left:606px"><h5>FOLLOW US</h5><ul><li>Friendsheet</li><li>Chirpline</li><li>Snapgrid</li><li>Workcircle</li></ul></div>
  <div class="f-col" style="left:807px"><h5>CONTACT US</h5><ul><li>Phone: 43 500 218 640</li><li>Email: office@kestrelyard</li></ul></div>
  <div class="f-rule"></div>
  <div class="copy">2022 Kestrel Yard. All Rights Reserved.</div>
</footer>

</body>
</html>
```